Designing a website that functions as the shop window for the various aspects of my business -...

I need a website, with separate webpages covering the different components of my practice (small animal consultancy, equine behaviour consultancy, legal case work and education provider). I have a website (www.petcalmstudio.ie) but I haven't updated it in recent years to reflect the newer developments / aspects of my business. Most of my work has been in Ireland but I would like to begin to create an international profile, particularly with regard to the legal casework and offering education within the international horse industry. My overall goal is to improve understanding of animals and animal behaviour, and by doing so, help to reduce the performance of behaviour problems, and also improve animal welfare as a result.

Target Market(s)

Horse and dog owners, horse riders, veterinary surgeons, solicitors

Industry/Entity Type

Legal

Logo Text

Text to be decided on

Number of Pages Required

5+ page

Font styles to use
Sans Serif
Decorative
Script

Colors

Designer to choose colors to be used in the design.

Requirements
Must have
• Relevant content from the attached Flyer including photos
• Use of the phrases:
• 'Understanding Animals'
• Improving animals lives through better understanding
• Science-based, up-to-date relevant information regarding animal behaviour
Nice to have
• 'Leading professional service educating people in understanding animals'
• Separate pages for 1) About, 2) Canine and Feline behaviour Consultancy 3) Equine Consultancy 4) Legal expert witness Consultancy 5) Education 6, FAQs
Should not have
• Prices of services (as these may change from time to time)

```html
<!DOCTYPE html>
<html lang="en">
<head>
<meta charset="utf-8">
<title>Pet Calm Studio</title>
<link rel="stylesheet" href="https://fonts.googleapis.com/css2?family=Oswald:wght@400;500;600&family=Poppins:wght@400;500;600&display=swap">
<style>
:root{
  --green:#2f8a3c;
  --green-dark:#1d6b2c;
  --green-light:#4aa23a;
  --orange:#f26a1f;
  --blue:#2a7fe0;
  --ink:#2b2b2b;
  --night:#151815;
  --grey:#ececec;
  --text:#555;
  --white:#fff;
}
*{margin:0;padding:0;box-sizing:border-box}
html,body{width:1200px;height:5263px;overflow:hidden}
body{position:relative;font-family:'Poppins',sans-serif;color:var(--text);background:var(--white)}
.abs{position:absolute}
.ph{position:absolute}
h1,h2,h3,.oswald{font-family:'Oswald',sans-serif;font-weight:400}

/* header */
.header{top:0;left:0;width:1200px;height:130px;background:var(--white)}
.call{left:140px;top:38px;text-align:right;width:160px;font-family:'Oswald',sans-serif;color:var(--ink)}
.call small{display:block;font-size:20px;line-height:24px}
.call b{font-size:24px;font-weight:600;line-height:30px}
.call-icon{left:306px;top:40px;width:46px;height:46px;border:2px solid var(--green);border-radius:50%}
.brand{left:420px;top:30px;height:60px;display:flex;align-items:center;gap:14px;font-family:'Oswald',sans-serif;font-size:34px;font-weight:500;color:var(--green)}
.brand i{width:22px;height:22px;background:var(--green);border-radius:50%;display:block}
.brand-line{left:420px;top:92px;width:360px;height:2px;background:var(--green)}
.estimate{left:836px;top:44px;width:218px;height:44px;border:2px solid var(--ink);border-radius:22px;font-family:'Oswald',sans-serif;font-size:17px;color:var(--ink);display:flex;align-items:center;justify-content:center;font-weight:500}

.nav{top:130px;left:0;width:1200px;height:53px;background:var(--ink);display:flex;align-items:center;padding-left:118px;gap:0}
.nav a{font-family:'Oswald',sans-serif;font-size:16px;color:var(--white);text-decoration:none;padding:0 16px;height:53px;display:flex;align-items:center}
.nav a.on{background:var(--green)}

/* hero */
.hero{top:183px;left:0;width:1200px;height:572px;background:linear-gradient(100deg,#3f6e2e 0%,#5f8f3a 40%,#c9c4b8 65%,#7da04a 100%)}
.hero h1{left:140px;top:155px;font-size:40px;color:var(--white)}
.hero ul{left:140px;top:225px;list-style:none;color:var(--white);font-size:16px;line-height:30px;width:420px}
.hero li{display:flex;gap:12px;align-items:flex-start}
.hero li svg{flex:none;margin-top:7px}
.hero .more{left:140px;top:390px;width:160px;height:46px;background:var(--green);color:var(--white);font-family:'Oswald',sans-serif;font-size:16px;display:flex;align-items:center;justify-content:center}
.arrow{width:36px;height:36px;border-radius:50%;background:rgba(0,0,0,.55)}

/* welcome */
.welcome{top:755px;left:0;width:1200px;height:666px;background:var(--grey)}
.welcome-photo{left:533px;top:108px;width:544px;height:421px;background:linear-gradient(135deg,#5a4a3a,#a8906f 55%,#6b5a48)}
.welcome-frame{left:560px;top:135px;width:540px;height:422px;border:4px solid var(--green);border-left:none;border-top:none}
.welcome-card{left:140px;top:150px;width:474px;height:330px;background:var(--white);padding:36px 26px;box-shadow:0 4px 14px rgba(0,0,0,.15)}
.welcome-card small{font-family:'Oswald',sans-serif;font-size:16px;color:var(--ink);letter-spacing:.5px}
.welcome-card h2{font-size:32px;font-weight:600;color:var(--ink);line-height:40px}
.welcome-card hr{border:none;height:3px;width:70px;background:var(--green);margin:6px 0 24px}
.welcome-card p{font-size:14px;line-height:26px}

/* section titles */
.title{left:0;width:1200px;text-align:center;font-size:36px;color:var(--ink)}
.divider{left:530px;width:140px;height:30px}

/* components */
.intro{left:180px;top:1623px;width:840px;text-align:center;font-size:14px;line-height:24px}
.bubble{border-radius:50%;color:var(--white);text-align:center;display:flex;flex-direction:column;align-items:center;justify-content:center;padding:0 36px}
.bubble h3{font-size:20px;font-weight:500;margin:44px 0 8px}
.bubble p{font-size:12px;line-height:19px}
.bubble .dot{position:absolute;bottom:-6px;left:50%;margin-left:-14px;width:28px;height:28px;border-radius:50%;background:var(--white);border:3px solid currentColor}
.hub{left:372px;top:1775px;width:464px;height:464px;border-radius:50%;background:radial-gradient(circle at 50% 45%,#f3e6d4,#c9b296 60%,#e6e6e6)}

/* equine */
.equine{top:2421px;left:0;width:1200px;height:740px}
.equine h2{left:0;top:160px;width:1200px;text-align:center;font-size:38px;color:var(--white)}
.equine p{left:170px;top:236px;width:860px;text-align:center;font-size:14px;line-height:25px;color:#ddd}
.video{left:147px;top:397px;width:909px;height:452px;background:linear-gradient(120deg,#3c4a2a,#6d8b45 50%,#2a2d22);border:5px solid var(--white);box-shadow:0 8px 24px rgba(0,0,0,.3)}
.play{left:413px;top:196px;width:84px;height:48px;background:var(--white);border-radius:10px}

/* blog */
.blog-title{font-weight:600}
.blog-title span{color:var(--green)}
.card{width:272px;height:368px;background:var(--white);box-shadow:0 2px 10px rgba(0,0,0,.15)}
.card .img{position:absolute;left:0;top:0;width:272px;height:222px}
.card .date{position:absolute;left:12px;top:12px;width:60px;height:62px;background:var(--green);color:var(--white);font-family:'Oswald',sans-serif;font-size:14px;line-height:20px;text-align:center;padding-top:10px}
.card h3{position:absolute;top:240px;left:20px;width:232px;text-align:center;font-family:'Poppins',sans-serif;font-size:15px;font-weight:600;color:var(--ink);line-height:22px}
.card p{position:absolute;top:296px;left:24px;width:224px;text-align:center;font-size:12px;line-height:18px}

/* gallery */
.gallery-bg{top:4000px;left:0;width:1200px;height:1000px}
.gallery-title{color:var(--white);font-weight:600}
.gallery-title span{font-weight:400}
.tile{border:2px solid var(--white)}

/* footer */
.footer{top:4877px;left:0;width:1200px;height:386px;background:var(--night)}
.contact{left:0;top:134px;width:1200px;display:flex;justify-content:center;gap:34px;color:var(--white);font-size:14px}
.contact span{display:flex;align-items:center;gap:8px}
.fnav{left:0;top:184px;width:1200px;text-align:center;color:var(--white);font-size:14px}
.fnav b{font-weight:400;padding:0 8px;color:#aaa}
.copy{left:0;top:230px;width:1200px;text-align:center;color:#ccc;font-size:13px}
.social{left:0;top:283px;width:1200px;display:flex;justify-content:center;gap:14px}
.social i{width:40px;height:40px;border:2px solid #888;border-radius:50%;display:block}
</style>
</head>
<body>

<header class="abs header">
  <div class="abs call"><small>Call Us</small><b>087 555 0148</b></div>
  <svg class="abs call-icon" viewBox="0 0 46 46" aria-hidden="true"><path d="M16 13c2 0 4 5 3 6l-2 2c1 3 4 6 7 7l2-2c1-1 6 1 6 3v3c0 1-1 2-3 2-9 0-17-8-17-17 0-2 1-3 2-3z" fill="var(--green)"/></svg>
  <div class="abs brand"><i></i>Pet Calm Studio</div>
  <div class="abs brand-line"></div>
  <div class="abs estimate">GET A FREE ESTIMATE!</div>
</header>

<nav class="abs nav">
  <a class="on">Home</a><a>About Us</a><a>Canine And Feline Behaviour Consultancy</a><a>Equine Consultancy</a><a>Legal Expert Witness Consultancy</a><a>Education</a><a>Contact Us</a>
</nav>

<section class="abs hero">
  <div class="ph" role="img" aria-label="Photo of a small scruffy dog running across green grass" style="inset:0"></div>
  <h1 class="abs">Pet Calm Studio</h1>
  <ul class="abs">
    <li><svg width="16" height="16" viewBox="0 0 16 16"><circle cx="8" cy="8" r="8" fill="#fff"/><path d="M4.5 8.2l2.3 2.3 4.7-4.8" stroke="var(--green)" stroke-width="2" fill="none"/></svg>Understanding Animals</li>
    <li><svg width="16" height="16" viewBox="0 0 16 16"><circle cx="8" cy="8" r="8" fill="#fff"/><path d="M4.5 8.2l2.3 2.3 4.7-4.8" stroke="var(--green)" stroke-width="2" fill="none"/></svg>Improving animals lives through better understanding</li>
    <li><svg width="16" height="16" viewBox="0 0 16 16"><circle cx="8" cy="8" r="8" fill="#fff"/><path d="M4.5 8.2l2.3 2.3 4.7-4.8" stroke="var(--green)" stroke-width="2" fill="none"/></svg>Science-based, up-to-date relevant information regarding animal behaviour</li>
  </ul>
  <div class="abs more">Get More Info</div>
  <svg class="abs arrow" style="left:70px;top:268px" viewBox="0 0 36 36"><path d="M21 11l-7 7 7 7" stroke="#fff" stroke-width="3" fill="none"/></svg>
  <svg class="abs arrow" style="left:1094px;top:268px" viewBox="0 0 36 36"><path d="M15 11l7 7-7 7" stroke="#fff" stroke-width="3" fill="none"/></svg>
</section>

<section class="abs welcome">
  <div class="abs welcome-frame"></div>
  <div class="abs welcome-photo" role="img" aria-label="Photo of a small terrier dog looking at the camera"></div>
  <div class="abs welcome-card">
    <small>WELCOME TO</small>
    <h2>PET CALM STUDIO</h2>
    <hr>
    <p>Animals have been used by humans for a variety of purposes, including as a source of food, for hunting, for mobility, to help win battles, for sport - and most recently, for companionship. Whether we are dog or cat lovers, horsesriders or owners, through the course of our relationship</p>
  </div>
</section>

<h2 class="abs title" style="top:1510px">Components of my practice</h2>
<svg class="abs divider" style="top:1580px" viewBox="0 0 140 30" aria-hidden="true"><path d="M0 15h50M90 15h50" stroke="var(--green)" stroke-width="2"/><circle cx="70" cy="15" r="8" fill="var(--green)"/></svg>
<p class="abs intro">Each service shares one aim: helping owners, riders, vets and solicitors understand why animals behave as they do, using science-based, up-to-date information.</p>

<div class="abs hub" role="img" aria-label="Photo of a small dog wearing glasses and a bow tie"></div>
<div class="abs bubble" style="left:161px;top:1768px;width:260px;height:260px;background:var(--green-light);color:var(--green-light)"><h3 style="color:#fff">Small Animal Consultancy</h3><p style="color:#fff">Calm, practical plans for dogs and cats with fear, aggression or house problems at home.</p><span class="dot"></span></div>
<div class="abs bubble" style="left:761px;top:1768px;width:260px;height:260px;background:var(--orange);color:var(--orange)"><h3 style="color:#fff">Equine Behaviour Consultancy</h3><p style="color:#fff">Handling, loading and ridden problems assessed with welfare and rider safety in mind.</p><span class="dot"></span></div>
<div class="abs bubble" style="left:172px;top:2067px;width:260px;height:260px;background:var(--blue);color:var(--blue)"><h3 style="color:#fff">Legal Case Work</h3><p style="color:#fff">Independent expert witness reports on animal behaviour for solicitors and the courts.</p><span class="dot"></span></div>
<div class="abs bubble" style="left:761px;top:2074px;width:260px;height:260px;background:var(--green-dark);color:var(--green-dark)"><h3 style="color:#fff">Education Provider</h3><p style="color:#fff">Courses and talks for owners, vets and the wider international horse industry.</p><span class="dot"></span></div>

<section class="abs equine">
  <svg class="abs" style="left:0;top:0" width="1200" height="740" viewBox="0 0 1200 740" aria-hidden="true">
    <path d="M0 0 Q300 70 620 40 T1200 40 V740 H0Z" fill="var(--night)"/>
    <path d="M0 0 Q150 50 320 52 Q140 44 0 20Z" fill="var(--green)"/>
    <path d="M0 610 Q400 700 760 650 T1200 600 V740 H0Z" fill="var(--green)"/>
    <path d="M0 630 Q400 720 760 670 T1200 622 V740 H0Z" fill="#fff"/>
  </svg>
  <h2 class="abs">Equine Training, Performance and Welfare</h2>
  <p class="abs">The Pet Calm Studio was established in 1994 by Niamh Carrow as an animal behaviour referral, consultancy and education provider dedicated to improving understanding of animal behaviour and welfare and investigating and resolving problem behaviours in a range of animal species.</p>
  <div class="abs video" role="img" aria-label="Video still of a horse grazing beside a black and white dog">
    <svg class="abs play" viewBox="0 0 84 48"><path d="M36 14l14 10-14 10z" fill="var(--ink)"/></svg>
  </div>
</section>

<h2 class="abs title blog-title" style="top:3342px">LATEST <span>BLOG</span></h2>
<svg class="abs divider" style="top:3408px" viewBox="0 0 140 30" aria-hidden="true"><path d="M0 15h50M90 15h50" stroke="var(--green)" stroke-width="2"/><circle cx="70" cy="15" r="8" fill="var(--green)"/></svg>

<article class="abs card" style="left:137px;top:3527px">
  <div class="img" role="img" aria-label="Photo of a rider with her horse" style="background:linear-gradient(135deg,#7a4a30,#3f6d3a)"></div>
  <div class="date">Oct 01<br>2018</div>
  <h3>Reading calm signals in the stable</h3>
  <p>Small changes in routine can ease stress and help horses settle better.</p>
</article>
<article class="abs card" style="left:463px;top:3527px">
  <div class="img" role="img" aria-label="Photo of a woman with a husky dog" style="background:linear-gradient(135deg,#b7b9a8,#6f8a4c)"></div>
  <div class="date">Oct 01<br>2018</div>
  <h3>Why puppies need early socialising</h3>
  <p>Gentle, varied experiences early on shape a confident, relaxed adult dog.</p>
</article>
<article class="abs card" style="left:790px;top:3527px">
  <div class="img" role="img" aria-label="Photo of a girl in a hat with a horse" style="background:linear-gradient(135deg,#e2b65a,#8a5a32)"></div>
  <div class="date">Oct 01<br>2018</div>
  <h3>Building trust from the ground up</h3>
  <p>Groundwork gives horse and handler a shared language before riding begins.</p>
</article>

<svg class="abs gallery-bg" viewBox="0 0 1200 1000" aria-hidden="true">
  <defs><linearGradient id="gg" x1="0" y1="0" x2="0" y2="1"><stop offset="0" stop-color="#2a8a3a"/><stop offset="1" stop-color="#15452a"/></linearGradient></defs>
  <path d="M0 30 Q300 90 600 60 T1200 0 V1000 H0Z" fill="url(#gg)"/>
</svg>
<h2 class="abs title gallery-title" style="top:4104px">OUR <span>GALLERY</span></h2>
<svg class="abs divider" style="top:4176px" viewBox="0 0 140 30" aria-hidden="true"><path d="M0 15h50M90 15h50" stroke="#fff" stroke-width="2"/><circle cx="70" cy="15" r="8" fill="#fff"/></svg>

<div class="abs tile" role="img" aria-label="Photo of a child riding a pony" style="left:144px;top:4256px;width:302px;height:248px;background:linear-gradient(135deg,#6e4a32,#4f7a3a)"></div>
<div class="abs tile" role="img" aria-label="Photo of a golden puppy on grass" style="left:446px;top:4256px;width:306px;height:248px;background:linear-gradient(135deg,#d9c9a0,#7fa055)"></div>
<div class="abs tile" role="img" aria-label="Photo of a woman with a horse at a stable door" style="left:752px;top:4256px;width:304px;height:248px;background:linear-gradient(135deg,#8a3a2a,#c9a28a)"></div>
<div class="abs tile" role="img" aria-label="Photo of a man hugging a labrador" style="left:144px;top:4504px;width:604px;height:251px;background:linear-gradient(135deg,#7a8a5a,#e0c49a 55%,#5a6a3a)"></div>
<div class="abs tile" role="img" aria-label="Photo of a collie leaping for a frisbee" style="left:748px;top:4504px;width:308px;height:251px;background:linear-gradient(135deg,#6f9a4a,#2f4a2a)"></div>

<footer class="abs footer">
  <div class="abs contact">
    <span><svg width="12" height="16" viewBox="0 0 12 16"><path d="M6 0a6 6 0 0 1 6 6c0 4-6 10-6 10S0 10 0 6a6 6 0 0 1 6-6z" fill="#fff"/><circle cx="6" cy="6" r="2.2" fill="var(--night)"/></svg>14 Harbour Row, Galway, H91 X2T4</span>
    <span><svg width="14" height="14" viewBox="0 0 14 14"><path d="M2 1c1 0 2.5 3 2 3.5L3 5.5c.8 2 2.5 3.7 4.5 4.5l1-1c.5-.5 3.5 1 3.5 2V12c0 .5-.5 1-1.5 1C5 13 1 9 1 3.5 1 2 1.5 1 2 1z" fill="#fff"/></svg>087 555 0148</span>
    <span><svg width="16" height="12" viewBox="0 0 16 12"><rect x="0" y="0" width="16" height="12" fill="#fff"/><path d="M0 0l8 6 8-6" stroke="var(--night)" fill="none"/></svg>hello@petcalmstudio.ie</span>
  </div>
  <div class="abs fnav">Home<b>|</b>About Us<b>|</b>Canine and Feline Behaviour Consultancy<b>|</b>Equine Consultancy<b>|</b>Education</div>
  <div class="abs copy">© 2018 Pet Calm Studio. All Rights Reserved.</div>
  <div class="abs social"><i></i><i></i><i></i><i></i><i></i></div>
</footer>

</body>
</html>
```